Luxury Home Builder looking for an Exciting Homes Portfolio

We have a number of custom homes that we have completed over the years, and we want to give prospective clients are colorful and exciting catalog of our previous homes. I will provide access to the dropbox with all the photos. Need to get as many photos of homes in the catalog as possible. Please use vandrelluxuryhomes.com for pictures, lots of them in the portfolio, projects in progress, spec homes are available. I will provide full files to the winner. Need a very hip catalog to give out at events, and marketing venues.

Target Market(s)

High Net Worth Individuals looking for luxury homes

Industry/Entity Type

Real Estate Development

Requirements
Must have
• Photos of our project, please use vandrelluxuryhomes.com to get the photos, and will provide access to full pictures on dropbox to the winner.
• Logo must be incorporated.
Nice to have
• Clarification, website is not for design, but for the purposes of getting the photos. this has to be a very cool portfolio.

```html
<!DOCTYPE html>
<html lang="en">
<head>
<meta charset="utf-8">
<title>Vandrel Luxury Homes – Portfolio Spread</title>
<link href="https://fonts.googleapis.com/css2?family=Open+Sans:wght@400;600&family=Oswald:wght@300&display=swap" rel="stylesheet">
<style>
  :root {
    --backdrop: #a9aebb;
    --paper: #f7f7f8;
    --paper-shade: #ececef;
    --ink: #1e1e22;
    --muted: #8a8c93;
    --accent-red: #e0403a;
    --accent-deep: #c8262b;
    --accent-orange: #e9702f;
  }
  * { margin: 0; padding: 0; box-sizing: border-box; }
  html, body { width: 1200px; height: 1200px; overflow: hidden; }
  body {
    background: var(--backdrop);
    font-family: "Open Sans", sans-serif;
    color: var(--ink);
    position: relative;
  }
  .spread {
    position: absolute;
    left: 80px; top: 230px;
    width: 1040px; height: 740px;
    background: var(--paper);
    box-shadow: 0 20px 40px rgba(40,44,56,.25);
  }
  .spread__gutter {
    position: absolute; left: 510px; top: 0; width: 20px; height: 100%;
    background: linear-gradient(90deg, transparent, rgba(0,0,0,.08), transparent);
    pointer-events: none;
  }
  .collage { position: absolute; inset: 0; width: 1040px; height: 740px; }
  .intro {
    position: absolute; left: 56px; top: 500px; width: 400px;
  }
  .intro__title {
    font-weight: 400; font-size: 24px; letter-spacing: .5px;
    text-transform: uppercase; margin-bottom: 10px;
  }
  .intro__body { font-size: 10.5px; line-height: 1.55; text-align: justify; }
  .brand {
    position: absolute; left: 56px; top: 662px;
    display: flex; align-items: center; gap: 14px;
  }
  .brand__dot { width: 34px; height: 34px; border-radius: 50%; background: var(--paper-shade); }
  .brand__name {
    font-family: "Oswald", sans-serif; font-weight: 300; font-size: 18px;
    letter-spacing: 1.5px; color: var(--muted); text-transform: uppercase;
  }
  .panel-name {
    position: absolute; left: 905px; top: 650px;
    font-family: "Oswald", sans-serif; font-weight: 300; font-size: 16px;
    letter-spacing: 2px; color: #ffffff; text-transform: uppercase;
  }
</style>
</head>
<body>
  <main class="spread">
    <svg class="collage" viewBox="0 0 1040 740" xmlns="http://www.w3.org/2000/svg">
      <defs>
        <linearGradient id="sky-villa" x1="0" y1="0" x2="0" y2="1">
          <stop offset="0" stop-color="#7ea3d4"/><stop offset=".45" stop-color="#e9e2d3"/><stop offset="1" stop-color="#8b7a63"/>
        </linearGradient>
        <linearGradient id="garden-pool" x1="0" y1="0" x2="0" y2="1">
          <stop offset="0" stop-color="#b9cfe4"/><stop offset=".4" stop-color="#6f8f4e"/><stop offset=".7" stop-color="#8fc9d8"/><stop offset="1" stop-color="#c9bfae"/>
        </linearGradient>
        <linearGradient id="facade" x1="0" y1="0" x2="1" y2="1">
          <stop offset="0" stop-color="#dcd3c2"/><stop offset="1" stop-color="#7d6a52"/>
        </linearGradient>
        <linearGradient id="chandelier" x1="0" y1="0" x2="1" y2="1">
          <stop offset="0" stop-color="#efe9e1"/><stop offset="1" stop-color="#b39b82"/>
        </linearGradient>
        <linearGradient id="woodwork" x1="0" y1="0" x2="1" y2="1">
          <stop offset="0" stop-color="#7a3c1f"/><stop offset=".6" stop-color="#a05a30"/><stop offset="1" stop-color="#c9b49a"/>
        </linearGradient>
        <linearGradient id="pool-villa" x1="0" y1="0" x2="0" y2="1">
          <stop offset="0" stop-color="#cfe0ee"/><stop offset=".35" stop-color="#eceae4"/><stop offset=".6" stop-color="#2ea6d8"/><stop offset="1" stop-color="#7fd0ec"/>
        </linearGradient>
        <linearGradient id="porch" x1="0" y1="0" x2="0" y2="1">
          <stop offset="0" stop-color="#e8e4d6"/><stop offset="1" stop-color="#a48f70"/>
        </linearGradient>
        <linearGradient id="lawn" x1="0" y1="0" x2="0" y2="1">
          <stop offset="0" stop-color="#5a90d8"/><stop offset=".45" stop-color="#d9d4bf"/><stop offset="1" stop-color="#5f9a2c"/>
        </linearGradient>
        <linearGradient id="dusk" x1="0" y1="0" x2="0" y2="1">
          <stop offset="0" stop-color="#4c4033"/><stop offset=".5" stop-color="#e9e4d8"/><stop offset="1" stop-color="#4f7b35"/>
        </linearGradient>
        <linearGradient id="red-panel" x1="0" y1="0" x2="1" y2="0">
          <stop offset="0" stop-color="var(--accent-red)"/><stop offset=".55" stop-color="var(--accent-orange)"/><stop offset="1" stop-color="var(--accent-deep)"/>
        </linearGradient>
      </defs>

      <polygon points="250,0 520,0 520,330 400,210 330,140" fill="url(#sky-villa)" role="img" aria-label="Photo: Mediterranean villa exterior with tiled roof and balconies"/>
      <polygon points="330,140 470,280 340,480 210,390 270,200" fill="url(#garden-pool)" role="img" aria-label="Photo: garden courtyard with pool and stone paving"/>
      <polygon points="400,210 520,330 520,560 440,480 470,280" fill="url(#facade)" role="img" aria-label="Photo: arched entry door of a stone facade"/>
      <polygon points="520,0 700,0 640,150 560,240 520,200" fill="url(#sky-villa)" role="img" aria-label="Photo: villa facade with arched windows"/>
      <polygon points="700,0 770,70 700,210 600,160 640,150" fill="url(#sky-villa)" opacity=".9" role="img" aria-label="Photo: balcony and rooftop detail"/>
      <polygon points="660,90 790,140 740,310 610,250" fill="url(#chandelier)" role="img" aria-label="Photo: crystal chandelier in a double-height foyer"/>
      <polygon points="600,250 740,310 700,470 560,420 540,330" fill="url(#woodwork)" role="img" aria-label="Photo: carved wood kitchen with arched windows"/>
      <polygon points="790,0 1040,0 1040,480 900,410 760,300 800,150" fill="url(#pool-villa)" role="img" aria-label="Photo: white villa with palm trees and swimming pool"/>
      <polygon points="700,330 900,410 860,560 720,520" fill="url(#porch)" role="img" aria-label="Photo: covered porch with columns and flowering shrubs"/>
      <polygon points="540,420 700,470 640,620 560,600 520,520" fill="url(#dusk)" role="img" aria-label="Photo: two-storey villa at dusk with lit windows"/>
      <polygon points="640,560 800,560 880,640 760,740 680,690" fill="url(#lawn)" role="img" aria-label="Photo: villa across a broad green lawn"/>
      <polygon points="840,520 960,470 1040,510 1040,740 930,740 860,630" fill="url(#red-panel)"/>
    </svg>
    <div class="spread__gutter"></div>

    <section class="intro">
      <h1 class="intro__title">Who We Are</h1>
      <p class="intro__body">At Vandrel, there are no easy answers, no pat formulas. We leave that sort of thing to the mass market developers. Each home we undertake is a one-of-a-kind, fully customized residence, designed to meet the specific desires of its residents. When you work with a limited universe of prospective clients, there is no room for error. Every home we build must measure up on every count. Because we know that our clients, our homebuyers, are our salespeople. Indeed, they are the only ‘sales force’ we have.</p>
    </section>

    <div class="brand">
      <span class="brand__dot"></span>
      <span class="brand__name">Casavella Villa</span>
    </div>
    <span class="panel-name">Vandrel</span>
  </main>
</body>
</html>
```